Interior Design for Every Day, Nora Whitfield Interior Design, LLC

We are looking for a website for an Interior Design Company targeted at higher income households. We prefer to work with clients that seek to amplify the architectural beauty of their interior space via interior design - while ensuring the space promotes easy living. For example: a kitchen should be lain out in an intuitive manner such that all utensils, cups and plates are easy to find. Living rooms should be arranged to promote conversation and/or watch TV, etc.... We have heavy reliance on the technical aspects of design (computer automated renderings). We like the look and feel of this website: https://www.brenthalvorsen.example/portfolioall

Target Market(s)

Upper HHI ($200,000+) in the Atlanta Metro Market. Customers are likely to be highly educated and from a variety of cultural backgrounds. Ages 35-60

Industry/Entity Type

Architecture

Font styles to use
Sans Serif

Colors

Designer to choose colors to be used in the design.

Requirements
Must have
• Landing Page, Page demonstrating how interior design fits into the architectural design process, About Us Page with contact info, Example Work Page and Tailored Client Page. Minimal work can be done on the About Us and example work pages. The tailored client page just needs a good layout (and easy uploads and download capability)
• Also to include:
• (1) The landing page should include a Design Philosophy Section and maybe a couple examples of our work and/or pictures you provide
• (2) The Design Process page should explain all steps of the architectural Design process and should explain where interior design/decorating fits into the Architectural process (see below attachments).
• (3) The Example work page should include areas for portfolio example uploads (to include 3 dimensional and 2 dimensional renderings, photos and videos).
• (4) Include a Password Protected, Secure Place where each individual client can store and retrieve documents and work product for their project (Should be a separate page). There should be sections (for each client) for:
• (a) there should be a client account creation requirement page that requires: FN, LN, Mobile, email, Work phone, Property address, City, Zip (for 3 properties), Spouse FN, Spouse LN, Child FN, LN (space for 5 children)
• (a) section: Legal & Invoices
• (b) section: Drawings & Renderings
• (c) section: Pin Ups (easy uploads of pictures from sites like snapboardia would be appreciated) - pin ups should be very easy for clients to put examples of what they like
• (5) Ability for admin to use personalized password and username to view, delete and edit client files (we utilize filecrate for document storage currently, and integration with filecrate would be a plus)
• (6) needs to be formatted and optimized for Mobile (iOs and android) viewing as well as Web
• (7) The site should be built with a hosting service contemplated. This service should be affordable (Less than $300 per annum)
• (8) most importantly the site should be minimalist with focus on user friendliness while being fashion forward
• (9) Website Color scheme should be White/Black/BlueGrey
• (10) The site must also include the ability to generate an invoice, based on client registration, electronically submit the invoice to the client via email (or print it), accept payment via coinvoy integration, and generate conformation email of payment to both client and admin (although coinvoy may already do this).
Nice to have
• Ability of example and client pages to be integrated with sites like snapbordia and filecrate. Ability to have some sort of section that self identifies the clients design style(s)...maybe a quiz or at lease a place where they can create a pinboard of images and colors they like (potentially by room)
Should not have
• Must look modern and be extremely quick/user friendly. Our clients are very busy.

```html
<!DOCTYPE html>
<html lang="en">
<head>
<meta charset="utf-8">
<title>Nora Whitfield Interior Design</title>
<link rel="stylesheet" href="https://fonts.googleapis.com/css2?family=Poppins:wght@600;700&family=Montserrat:wght@400;500&display=swap">
<style>
  :root {
    --white: #ffffff;
    --ink: #5a5a5a;
    --blue-grey: #84b0b0;
    --hero-dark: #3f4852;
    --hero-mid: #8a8f95;
    --hero-light: #cfcfcf;
  }
  * { margin: 0; padding: 0; box-sizing: border-box; }
  html, body { width: 1200px; height: 771px; overflow: hidden; background: var(--white); }
  body { position: relative; font-family: "Montserrat", sans-serif; }

  .hero {
    position: absolute; left: 0; top: 0; width: 1200px; height: 543px;
    background:
      linear-gradient(rgba(20,24,30,0.28), rgba(20,24,30,0.28)),
      linear-gradient(180deg, var(--hero-dark) 0%, #5b636c 38%, var(--hero-mid) 62%, var(--hero-light) 82%, #9a9690 100%);
  }
  .brand {
    position: absolute; left: 101px; top: 39px; display: flex; align-items: center; gap: 8px;
    color: var(--white); font-family: "Montserrat", sans-serif; font-weight: 500;
    font-size: 14px; line-height: 18px;
  }
  .brand-mark { width: 10px; height: 10px; background: var(--white); display: block; }

  .main-nav {
    position: absolute; right: 99px; top: 39px; display: flex; gap: 24px;
  }
  .main-nav a {
    color: var(--white); text-decoration: none;
    font-family: "Poppins", sans-serif; font-weight: 600; font-size: 13.5px; line-height: 18px;
  }

  .hero-title {
    position: absolute; left: 0; top: 246px; width: 1200px; text-align: center;
    color: var(--white); font-family: "Poppins", sans-serif; font-weight: 700;
    font-size: 47px; line-height: 66px; letter-spacing: 2px;
  }

  .philosophy { position: absolute; left: 0; top: 570px; width: 1200px; text-align: center; }
  .philosophy h2 {
    font-family: "Poppins", sans-serif; font-weight: 600; font-size: 32px;
    color: var(--blue-grey); letter-spacing: 1px; line-height: 50px;
  }
  .philosophy p {
    width: 908px; margin: 12px auto 0; font-size: 10.9px; line-height: 20.5px;
    color: var(--ink); text-align: justify; text-align-last: center;
  }

  .site-footer {
    position: absolute; left: 0; top: 718px; width: 1200px; height: 53px;
    background: var(--blue-grey); color: var(--white);
    font-weight: 500; font-size: 12px; text-align: center; line-height: 53px;
  }
</style>
</head>
<body>
  <header class="hero" role="img" aria-label="Photograph of a bright living room with a grey sofa, patterned cushions, wicker table, white cabinet and orange chairs">
    <div class="brand">
      <span class="brand-mark"></span>
      <span class="brand-name">Nora Whitfield Interior Design</span>
    </div>
    <nav class="main-nav">
      <a href="#">Home</a>
      <a href="#">Process</a>
      <a href="#">About us</a>
      <a href="#">Example Works</a>
      <a href="#">Client Corner</a>
      <a href="#">Contact us</a>
    </nav>
    <h1 class="hero-title">Design Is Thinking Made<br>Visual</h1>
  </header>

  <section class="philosophy">
    <h2>Design Philosophy</h2>
    <p>Lorem Ipsum is simply dummy text of the printing and typesetting industry. Lorem Ipsum has been the industry's standard dummy text ever since the 1500s, when an unknown printer took a galley of type and scrambled it to make a type specimen book. It has survived not only five centuries, but also the leap into electronic ypese tting, remaining essentially unchanged.</p>
  </section>

  <footer class="site-footer">© 2017 Nora Whitfield Interior Design. All Rights Reserved.</footer>
</body>
</html>
```